Brightway Haul & Upkeep Services, are a company that offers a 'one stop shop' pre-move clean up a

I have already selected a logo which I would like on the front of the business cards along with phone numbers, web address and email which are:
0487650392
www.brightwayhaul.com.au
brightwayhaulandupkeep@mailbox.example

On the back of the card I would like to list some of the types of service we offer (clean - move - repairs/maintenance) which are:
CLEAN - windows, gutters, solar panels, driveways/paths, carpets.
MOVE - Small/medium size house/office moves, large item pick-up & delivery, yard clean-up and removal.
General maintenance and repairs.

I would like the blue logo on a gray background.

Thanks

```html
<!DOCTYPE html>
<html lang="en">
<head>
<meta charset="utf-8">
<title>Brightway Haul &amp; Upkeep Services – Business Card</title>
<link rel="stylesheet" href="https://fonts.googleapis.com/css2?family=Titillium+Web:wght@700&family=Open+Sans:wght@400;600;700&display=swap">
<style>
  :root {
    --brand-blue: #2a6db8;
    --brand-light: #7ab4e4;
    --ink: #222426;
    --card: #ffffff;
    --backdrop: #e4e6e8;
  }
  * { box-sizing: border-box; margin: 0; padding: 0; }
  html, body {
    width: 1200px; height: 373px; overflow: hidden;
    background: var(--backdrop);
  }
  .canvas { position: relative; width: 1200px; height: 373px; }
  .card {
    position: absolute; top: 30px; width: 547px; height: 312px;
    background: var(--card); overflow: hidden;
    box-shadow: 0 2px 6px rgba(0,0,0,.18);
  }
  .card--front { left: 36px; }
  .card--back { left: 613px; }

  .brand-name {
    position: absolute; left: 0; right: 0; text-align: center;
    font-family: "Titillium Web", sans-serif; font-weight: 700;
    color: var(--brand-blue); text-transform: uppercase; line-height: 1.05;
  }
  .card--front .brand-name { top: 78px; font-size: 36px; padding-left: 0; }
  .card--back .brand-name { top: 70px; font-size: 38px; }

  .contact {
    position: absolute; top: 208px; left: 0; width: 547px; height: 46px;
    font-family: "Open Sans", sans-serif; color: var(--ink);
  }
  .contact__phone {
    position: absolute; right: 345px; top: 13px; font-size: 14px;
    display: flex; align-items: center; gap: 5px;
  }
  .contact__divider {
    position: absolute; left: 213px; top: 0; width: 1px; height: 46px; background: #9a9a9a;
  }
  .contact__lines { position: absolute; left: 222px; top: 1px; }
  .contact__line { display: flex; align-items: center; gap: 5px; white-space: nowrap; }
  .contact__web { font-size: 15px; letter-spacing: .6px; margin-bottom: 3px; }
  .contact__mail { font-size: 11.5px; }
  .icon { width: 11px; height: 11px; flex: none; }

  .footer-bands { position: absolute; left: 0; bottom: 0; width: 547px; height: 18px; }

  .services-title {
    position: absolute; top: 204px; left: 0; right: 0; text-align: center;
    font-family: "Open Sans", sans-serif; font-weight: 700; font-size: 21px;
    letter-spacing: 1.8px; color: var(--brand-blue);
  }
  .services {
    position: absolute; top: 245px; left: 0; right: 0; list-style: none;
    font-family: "Open Sans", sans-serif; font-weight: 600; font-size: 16px;
    color: var(--ink); text-align: center;
  }
  .services__row { margin-bottom: 6px; }
  .services__item { display: inline-block; margin: 0 12px; }
  .services__item::before { content: "•"; color: var(--brand-blue); margin-right: 6px; }
</style>
</head>
<body>
<main class="canvas">

  <section class="card card--front" aria-label="Card front">
    <h1 class="brand-name">Brightway Haul<br>&amp; Upkeep Services</h1>

    <div class="contact">
      <div class="contact__phone">
        <svg class="icon" viewBox="0 0 12 12" aria-hidden="true"><path d="M3 1 L5 3.5 L4 5 Q5.5 7 7 8 L8.5 7 L11 9 L9.5 11 Q4 10.5 1 2.5 Z" fill="var(--brand-blue)"/></svg>
        <span>0487650392</span>
      </div>
      <div class="contact__divider"></div>
      <div class="contact__lines">
        <div class="contact__line contact__web">
          <svg class="icon" viewBox="0 0 12 12" aria-hidden="true"><circle cx="6" cy="6" r="5.2" fill="none" stroke="var(--brand-blue)" stroke-width="1.3"/><path d="M1 6h10M6 1v10" stroke="var(--brand-blue)" stroke-width="1"/></svg>
          <span>www.brightwayhaul.com.au</span>
        </div>
        <div class="contact__line contact__mail">
          <svg class="icon" viewBox="0 0 12 12" aria-hidden="true"><rect x="1" y="3" width="10" height="7" fill="var(--brand-blue)"/><path d="M1 3 L6 7 L11 3" stroke="#fff" stroke-width="1" fill="none"/></svg>
          <span>brightwayhaulandupkeep@mailbox.example</span>
        </div>
      </div>
    </div>

    <svg class="footer-bands" viewBox="0 0 547 18" preserveAspectRatio="none" aria-hidden="true">
      <polygon points="0,2 230,2 214,18 0,18" fill="var(--brand-light)"/>
      <polygon points="238,2 547,2 547,18 222,18" fill="var(--brand-blue)"/>
    </svg>
  </section>

  <section class="card card--back" aria-label="Card back">
    <h2 class="brand-name">Brightway Haul<br>&amp; Upkeep Services</h2>
    <h3 class="services-title">Services we offer</h3>
    <ul class="services">
      <li class="services__row"><span class="services__item">Clean</span><span class="services__item">Move</span></li>
      <li class="services__row"><span class="services__item">General Maintenance And Repairs.</span></li>
    </ul>
  </section>

</main>
</body>
</html>
```